Marwick Law Letterhead

We need a new letterhead design for a Law Firm. The address for the law firm is 1475 Calloway Street, Suite 210, Houston, Texas 77041. Phone Number: 832-361-9027; Fax Number: 832-614-7359. The logo is uploaded to the project.

```html
<!DOCTYPE html>
<html lang="en">
<head>
<meta charset="utf-8">
<title>Marwick Law Letterhead</title>
<link href="https://fonts.googleapis.com/css2?family=Roboto:wght@400;500&display=swap" rel="stylesheet">
<style>
  :root {
    --backdrop: #e9e9ea;
    --paper: #f7f7f6;
    --navy: #1f2a5c;
    --red: #c8182a;
    --ink: #3a3a3c;
    --band-text: #ffffff;
  }
  * { margin: 0; padding: 0; box-sizing: border-box; }
  html, body { width: 1200px; height: 795px; overflow: hidden; }
  body {
    background: var(--backdrop);
    font-family: "Roboto", Arial, sans-serif;
    color: var(--ink);
    position: relative;
  }
  .letterhead {
    position: absolute;
    left: 330px;
    top: 16px;
    width: 540px;
    height: 763px;
    background: var(--paper);
    box-shadow: 0 2px 10px rgba(0,0,0,0.08);
  }
  .contact-band {
    position: absolute;
    left: 0;
    top: 58px;
    width: 330px;
    height: 34px;
    background: linear-gradient(90deg, var(--navy) 0%, #5a2250 55%, var(--red) 100%);
    color: var(--band-text);
    font-size: 8.5px;
    line-height: 12px;
    padding: 5px 0 0 22px;
  }
  .contact-band .line { display: flex; align-items: center; gap: 4px; }
  .contact-band svg { width: 7px; height: 7px; fill: var(--band-text); flex: none; }
  .brand {
    position: absolute;
    left: 340px;
    top: 52px;
    display: flex;
    align-items: center;
    gap: 7px;
  }
  .brand-dot {
    width: 22px; height: 22px; border-radius: 50%;
    background: var(--navy);
  }
  .brand-name {
    font-size: 22px;
    font-weight: 500;
    color: var(--navy);
    letter-spacing: 0.5px;
    line-height: 1;
  }
  .brand-tagline {
    position: absolute;
    left: 369px;
    top: 80px;
    font-size: 5.5px;
    letter-spacing: 0.6px;
    text-transform: uppercase;
    color: var(--red);
    border-top: 0.6px solid var(--red);
    padding-top: 2px;
    width: 120px;
  }
  .letter-body {
    position: absolute;
    left: 70px;
    top: 190px;
    width: 400px;
    font-size: 9.5px;
    line-height: 13.5px;
  }
  .salutation { font-size: 12.5px; margin-bottom: 10px; }
  .letter-body p { margin-bottom: 12px; }
  .closing { margin-top: 16px; }
  .signature {
    display: block;
    margin-top: 6px;
    width: 80px;
    height: 30px;
    background: linear-gradient(90deg, rgba(31,42,92,0.15), rgba(31,42,92,0.05));
  }
</style>
</head>
<body>
  <main class="letterhead">
    <div class="contact-band">
      <div class="line">
        <svg viewBox="0 0 10 10" aria-hidden="true"><path d="M5 0a3.6 3.6 0 0 0-3.6 3.6C1.4 6.3 5 10 5 10s3.6-3.7 3.6-6.4A3.6 3.6 0 0 0 5 0zm0 5a1.4 1.4 0 1 1 0-2.8A1.4 1.4 0 0 1 5 5z"/></svg>
        <span>1475 Calloway Street, Suite 210, Houston, Texas 77041</span>
      </div>
      <div class="line">
        <svg viewBox="0 0 10 10" aria-hidden="true"><path d="M2 0.5l2 2-1 1.3c.6 1.2 1.6 2.2 2.8 2.8L7 5.6l2 2-1.2 1.6C4.5 9 1 5.5.8 1.7z"/></svg>
        <span>832-361-9027</span>
        <svg viewBox="0 0 10 10" aria-hidden="true"><path d="M2 1h5v2H2zM1 3.5h8v4H7.5V9h-5V7.5H1zm2.5 2.5v2h3V6z"/></svg>
        <span>832-614-7359</span>
      </div>
    </div>

    <div class="brand">
      <span class="brand-dot"></span>
      <span class="brand-name">Marwick Law</span>
    </div>
    <div class="brand-tagline">Trusted counsel for every case</div>

    <section class="letter-body">
      <div class="salutation">Dear Mr. Ellison,</div>
      <p>Lorem ipsum dolor sit amet, consectetur adipiscing elit. Donec orci purus, luctus vitae dignissim eu, iaculis sed purus. Vivamus faucibus, ipsum nec aliquet viverra, leo mauris condimentum ligula, sit amet sagittis enim ligula quis arcu. Nam egestas tortor id nisi porttitor mattis. In tortor ante, ultricies in suscipit a, tempus non massa. Vivamus et auctor mi. Fusce vel massa nulla. Phasellus nec eros mauris, et scelerisque orci.</p>
      <p>Donec malesuada orci vitae nulla accumsan porta a id massa. Quisque accumsan iaculis magna sit amet fringilla. Maecenas consequat, magna eget tincidunt semper, odio nibh rutrum mi, id feugiat ante nisi eu risus. Vestibulum nunc orci, rhoncus a placerat in, ultricies in mi. Cras mattis varius eros, vel fringilla nisi suscipit eget. Quisque scelerisque sagittis nulla at porttitor.</p>
      <p>Sed id augue vitae urna euismod commodo aliquet a quam. Pellentesque arcu velit, cursus et malesuada ut, consequat et diam. Nullam erat sem, rhoncus id ullamcorper vitae, rhoncus et arcu. In ultricies ultricies nulla, ut rutrum nisl iaculis at. Donec eu magna a metus ornare faucibus. Fusce aliquet faucibus ultricies. Morbi semper, est id tincidunt gravida, sem arcu adipiscing lacus, ac bibendum nulla leo eu purus. Quisque nec diam sed risus consectetur accumsan quis quis nibh. Vestibulum id purus lorem.</p>
      <div class="closing">Sincerely,</div>
      <span class="signature" role="img" aria-label="Handwritten signature"></span>
    </section>
  </main>
</body>
</html>
```